IT Company needs full suite of stationery

Our company 4627 Vantor Holdings Inc. is an IT company based in Toronto, Canada. Based on our logo we would like to see business cards(front and back), letterhead, envelope, brochure template. Design would be simple, not too bright, modern but can be used for many years, good theme throughout. Our official logo is the the fullcolor_a, full company name is 4627 Vantor Holdings Inc., Please include full company name on all pieces. Logo can be modified to be the graphic only with the "4627 Holdings", I have cropped it myself for a couple files but I am no designer. We will provide lots of feedback so post early and often.

Project Deadline Extended
Reason: Very busy around the holidays, like a lot of the designs currently submitted, will definitely be picking one. Thanks for your submissions and merry Christmas and Happy New Year to everyone.

Industry/Entity Type

Business

```html
<!DOCTYPE html>
<html lang="en">
<head>
<meta charset="utf-8">
<title>4627 Vantor Holdings Inc. Letterhead</title>
<link href="https://fonts.googleapis.com/css2?family=Montserrat:wght@400;600&family=Tinos:ital,wght@0,400;0,700;1,400&display=swap" rel="stylesheet">
<style>
  :root {
    --backdrop: #e4e5e6;
    --paper: #ffffff;
    --green: #3f9a35;
    --ink: #1c1c1c;
    --charcoal: #3a3b3d;
    --muted: #6b6d70;
    --signature-fill: #d9dadb;
  }
  * { margin: 0; padding: 0; box-sizing: border-box; }
  html, body { width: 1200px; height: 909px; overflow: hidden; background: var(--backdrop); }
  .letterhead {
    position: absolute; left: 296px; top: 24px;
    width: 608px; height: 860px;
    background: var(--paper);
    box-shadow: 0 6px 24px rgba(0,0,0,.12);
    overflow: hidden;
  }
  .contact {
    position: absolute; left: 400px; top: 54px; width: 180px;
    font-family: "Montserrat", sans-serif; font-size: 6.5px; line-height: 10px; color: var(--muted);
  }
  .contact .company { font-weight: 600; color: var(--charcoal); }
  .contact .icon {
    display: inline-block; width: 5px; height: 5px; background: var(--green);
    margin-right: 5px; vertical-align: middle;
  }
  .brand {
    position: absolute; left: 56px; top: 160px;
    display: flex; align-items: center; gap: 8px;
  }
  .brand-dot { width: 26px; height: 26px; border-radius: 50%; background: var(--green); }
  .brand-name {
    font-family: "Montserrat", sans-serif; font-weight: 600;
    font-size: 17px; color: var(--charcoal); letter-spacing: .5px;
  }
  .letter {
    position: absolute; left: 62px; top: 246px; width: 486px;
    font-family: "Tinos", serif; font-size: 12.8px; line-height: 15.4px; color: var(--ink);
    text-align: justify;
  }
  .letter p { margin-bottom: 14px; }
  .closing { margin-top: 22px; margin-left: 222px; text-align: left; }
  .closing p { margin: 0; }
  .signature {
    display: block; width: 92px; height: 28px; margin: 8px 0 4px;
    background: var(--signature-fill); border-radius: 3px;
  }
  .rule-green { position: absolute; left: 0; right: 0; top: 788px; height: 4px; background: var(--green); }
  .footer-band {
    position: absolute; left: 0; right: 0; top: 800px; height: 60px;
    background: var(--charcoal);
    display: flex; align-items: center; justify-content: flex-end; padding-right: 34px;
  }
  .footer-web { font-family: "Montserrat", sans-serif; font-size: 10px; color: #ffffff; letter-spacing: 1px; }
</style>
</head>
<body>
  <main class="letterhead">
    <div class="contact">
      <span class="company">4627 Vantor Holdings Inc.</span><br>
      Harbourfront Way 63 M5J 2N8<br>
      Toronto Ontario Canada<br>
      <span class="icon"></span>+1 416 555 0134<br>
      <span class="icon"></span>+1 416 555 0178<br>
      <span class="icon"></span>info@4627holdings.com
    </div>

    <div class="brand">
      <span class="brand-dot"></span>
      <span class="brand-name">4627 Holdings</span>
    </div>

    <article class="letter">
      <p>Gentlemen,</p>
      <p>Enclosed I have the honor to send you an article which I should be pleased if you would accept for the &ldquo;Northern Review.&rdquo; I am <em>desperately</em> pushed for money; and in the event of Mr. Hallworth&rsquo;s liking the &ldquo;Landscape-Garden&rdquo; I would take it as an especial favor if you would mail me the amount due for it, so as to reach me here by the 21st, on which day I shall need it. Can you possibly oblige me in this? If you accept the paper I presume you will allow me your usual sum, whatever that is for similar contributions&mdash;but I set no price&mdash;leaving all to your own liberality. The piece will make 8 of your pages and rather more.</p>
      <p>Will you be kind enough to put the best possible interpretation upon my behavior while in N-York? You must have conceived a <em>queer</em> idea of me&mdash;but the simple truth is that Bramley would insist upon <em>the juleps</em>, and I knew not what I was either doing or saying. The Review of Corwin, which I offered you was deficient in a &frac12; page of commencement, which I had written to supersede the old beginning, and which gave the article the character of a general and retrospective review. No wonder you did not take it&mdash;I would have been very much mortified if you had. I hope to see you at some future time, under better auspices.</p>
      <div class="closing">
        <p>In the meantime I remain</p>
        <p>Yours very truly,</p>
        <span class="signature" role="img" aria-label="Handwritten signature"></span>
        <p>Edwin A. Marlowe</p>
      </div>
    </article>

    <div class="rule-green"></div>
    <footer class="footer-band">
      <span class="footer-web">www.4627holdings.com</span>
    </footer>
  </main>
</body>
</html>
```